Veranix - Solution provider in business consulting

Veranix is a swiss based company providing solutions for developing markets. The business covers various fields of business consulting, such as supply chain, product costs, quality management and manufacturing management. The Business operates in a efficient, straight and solution oriented manner.
The final design should communicate these characteristics. Asian people as well as as western people shall identify the qualities of the company at first sight.
The customer needs business cards with a simple view but an recognizable design, printed in high quality. Engraved elements such as the globe or simple words are possible.
Available colors are: (RAL)
102/102/102
51/102/102
153/204/153
255/102/51
Font: Calibri

```html
<!DOCTYPE html>
<html lang="en">
<head>
<meta charset="utf-8">
<title>Veranix – Business Card</title>
<link rel="stylesheet" href="https://fonts.googleapis.com/css2?family=Carlito:wght@400;700&display=swap">
<style>
  :root {
    --paper: #ffffff;
    --card: #4a4a4a;
    --band: #c5c5c5;
    --text: #ffffff;
    --mark: #6a6a6a;
    --trim: #1a1a1a;
  }
  html, body {
    margin: 0;
    padding: 0;
    width: 1200px;
    height: 843px;
    overflow: hidden;
    background: var(--paper);
    font-family: "Carlito", "Calibri", sans-serif;
  }
  .sheet {
    position: relative;
    width: 1200px;
    height: 843px;
  }
  .crop-marks {
    position: absolute;
    inset: 0;
  }
  .crop-marks line {
    stroke: var(--trim);
    stroke-width: 1;
  }
  .card {
    position: absolute;
    left: 98px;
    top: 133px;
    width: 968px;
    height: 572px;
    background: var(--card);
  }
  .card-edge {
    position: absolute;
    left: 1066px;
    top: 133px;
    width: 34px;
    height: 572px;
    background: var(--band);
  }
  .brand-band {
    position: absolute;
    left: 98px;
    top: 340px;
    width: 440px;
    height: 157px;
    background: var(--band);
    display: flex;
    align-items: center;
    justify-content: center;
    gap: 18px;
  }
  .brand-dot {
    width: 46px;
    height: 46px;
    border-radius: 50%;
    background: var(--mark);
  }
  .brand-name {
    font-size: 70px;
    font-weight: 400;
    color: var(--mark);
    line-height: 1;
    letter-spacing: 1px;
  }
  .line {
    position: absolute;
    color: var(--text);
    font-size: 30px;
    line-height: 1;
    white-space: nowrap;
    text-align: right;
    display: flex;
    align-items: center;
    justify-content: flex-end;
    gap: 14px;
  }
  .details .line { right: 222px; }
  .address .line { right: 667px; }
  .person-name { font-weight: 700; }
  .icon {
    width: 30px;
    height: 28px;
    fill: none;
    stroke: var(--text);
    stroke-width: 2;
  }
  .icon .solid { fill: var(--text); stroke: none; }
</style>
</head>
<body>
<div class="sheet">
  <svg class="crop-marks" width="1200" height="843" viewBox="0 0 1200 843" aria-hidden="true">
    <line x1="84" y1="0" x2="84" y2="72"/>
    <line x1="117" y1="34" x2="117" y2="93"/>
    <line x1="0" y1="83" x2="73" y2="83"/>
    <line x1="35" y1="116" x2="94" y2="116"/>
    <line x1="1083" y1="34" x2="1083" y2="93"/>
    <line x1="1116" y1="0" x2="1116" y2="72"/>
    <line x1="1129" y1="83" x2="1200" y2="83"/>
    <line x1="1107" y1="116" x2="1166" y2="116"/>
    <line x1="84" y1="771" x2="84" y2="843"/>
    <line x1="117" y1="749" x2="117" y2="809"/>
    <line x1="0" y1="759" x2="73" y2="759"/>
    <line x1="35" y1="725" x2="94" y2="725"/>
    <line x1="1083" y1="749" x2="1083" y2="809"/>
    <line x1="1116" y1="771" x2="1116" y2="843"/>
    <line x1="1129" y1="759" x2="1200" y2="759"/>
    <line x1="1107" y1="725" x2="1166" y2="725"/>
  </svg>

  <div class="card"></div>
  <div class="card-edge"></div>

  <div class="brand-band">
    <span class="brand-name">veranix</span>
    <span class="brand-dot"></span>
  </div>

  <div class="details">
    <div class="line person-name" style="top:203px">Marco Lenz</div>
    <div class="line person-role" style="top:239px">CEO</div>

    <div class="line" style="top:365px">
      <svg class="icon" viewBox="0 0 30 28" aria-hidden="true">
        <rect x="8" y="2" width="13" height="23" rx="2" transform="rotate(-20 15 14)"/>
      </svg>
      +41 79 555 0182
    </div>
    <div class="line" style="top:409px">
      <svg class="icon" viewBox="0 0 30 28" aria-hidden="true">
        <path class="solid" d="M3 9c0-4 24-4 24 0v3h-6V9H9v3H3z"/>
        <path class="solid" d="M7 13h16l3 11H4z"/>
      </svg>
      +41 71 555 0347
    </div>
    <div class="line" style="top:453px">
      <svg class="icon" viewBox="0 0 30 28" aria-hidden="true">
        <path d="M3 12 15 4l12 8v12H3z"/>
        <path d="M3 12l12 8 12-8"/>
      </svg>
      marco.lenz@veranix.ch
    </div>

    <div class="line" style="top:611px">www.veranix.ch</div>
  </div>

  <div class="address">
    <div class="line" style="top:511px">Veranix GmbH</div>
    <div class="line" style="top:547px">Feldstrasse 18</div>
    <div class="line" style="top:583px">9215 Lindenau</div>
    <div class="line" style="top:618px">Switzerland</div>
  </div>
</div>
</body>
</html>
```